eBook-Cover für Thriller gesucht
An dieser Stelle ein großes Lob und vielen Dank an die Designerin Larosa. Auch das zweite Buchcover ist wieder überaus gelungen, eine ganz tolle Arbeit. Auch die angenehme Zusammenarbeit war mir, wie schon beim ersten Auftrag, eine Freude. Ebenso hervorzuheben ist die Schnelligkeit und Kreativität, mit der die Designerin auf Änderungswünsche reagiert. Als Auftraggeber gebe ich verdiente fünf Sterne und bin mit dem Ergebnis wirklich sehr zufrieden.
Zielgruppe
Ich bin Autor. Zielgruppe sind (anspruchsvolle) Leser/innen von Thrillern und Kriminalromanen im ebook-Bereich.
Aufgabenstellung
- Gesucht wird ein ebook-Cover für einen Thriller mit dem Titel 'Kaltgrund'
- Grobe Aufteilung siehe Skizzen
- Fokus des Covers liegt auf dem Buchtitel und dem Motiv ('Blauer Drachen')
- Hintergrund eher hell, Assoziation mit zarter Eisfläche mit angedeuteten Rissen vom Hauptmotiv ausgehend. Dadurch auch Tiefe und Dreidimensionalität. (Beispiel zum Hintergrund: 'Schattenfrist' von Heinrich Wendel, jedoch ohne Blut )
-Titelschrift groß, Stil 'gekratzt' bzw. 'gestrichelt', (Schriftart ähnlich wie Autorenname bei 'Die Schleuse' von Matthias Kolbe). Schrift groß und 'treppenförmig' neben dem Hauptmotiv angeordnet. Schriftfarbe schwarz/dunkelblau, ähnlich Hauptmotiv (Bsp.: 'Schwarzeid' von Heinrich Wendel)
Hauptmotiv ist der vom rechten Coverrand hineinragende 'Blaue Drachen' (Glaucus atlanticus, siehe hochgeladenes Beispielbild von Wissnetz)
- Schriftart von Autorenname und Genre eher klar
- eigene Detailvorschläge zur Optimierung des Ergebnisses möglich bzw. erwünscht

```html
<!DOCTYPE html>
<html lang="de">
<head>
<meta charset="utf-8">
<title>Kaltgrund – Thriller</title>
<link rel="stylesheet" href="https://fonts.googleapis.com/css2?family=Cinzel:wght@500;700&family=Cabin+Sketch:wght@700&display=swap">
<style>
  :root {
    --ice-light: #eef6fa;
    --ice-mid: #b9d3e0;
    --ice-deep: #5f8aa3;
    --ink-navy: #131b33;
    --title-blue: #1b2c9c;
    --dragon-dark: #1e2a5c;
    --dragon-mid: #4f6fae;
    --dragon-pale: #a9bfd8;
    --crack: #101418;
  }
  html, body {
    margin: 0;
    padding: 0;
    width: 724px;
    height: 1200px;
    overflow: hidden;
    background: var(--ice-light);
  }
  .cover {
    position: relative;
    width: 724px;
    height: 1200px;
    overflow: hidden;
  }
  .ice-surface {
    position: absolute;
    inset: 0;
    background:
      radial-gradient(ellipse 60% 45% at 50% 55%, var(--ice-light) 0%, rgba(238,246,250,0) 70%),
      linear-gradient(135deg, var(--ice-deep) 0%, var(--ice-mid) 30%, var(--ice-light) 55%, var(--ice-mid) 80%, var(--ice-deep) 100%);
  }
  .cracks {
    position: absolute;
    inset: 0;
    width: 724px;
    height: 1200px;
  }
  .cracks path {
    fill: none;
    stroke: var(--crack);
    stroke-width: 2.2;
    stroke-linejoin: round;
  }
  .cracks .fine {
    stroke-width: 1;
    opacity: 0.45;
  }
  .blue-dragon {
    position: absolute;
    left: 294px;
    top: 98px;
    width: 430px;
    height: 560px;
    background:
      radial-gradient(ellipse 45% 14% at 70% 38%, var(--dragon-dark) 0%, var(--dragon-mid) 55%, rgba(79,111,174,0) 100%),
      radial-gradient(ellipse 55% 45% at 60% 50%, rgba(169,191,216,0.75) 0%, rgba(169,191,216,0) 75%);
  }
  .author {
    position: absolute;
    top: 40px;
    left: 0;
    width: 724px;
    text-align: center;
    font-family: 'Cinzel', serif;
    font-weight: 500;
    font-size: 66px;
    letter-spacing: 1px;
    color: var(--ink-navy);
    margin: 0;
    white-space: nowrap;
  }
  .title {
    margin: 0;
    font-family: 'Cabin Sketch', cursive;
    font-weight: 700;
    color: var(--title-blue);
    text-shadow: 0 0 14px rgba(255,255,255,0.9);
  }
  .title span {
    position: absolute;
    display: block;
    font-size: 250px;
    line-height: 1;
    white-space: nowrap;
    transform-origin: left top;
    transform: skewX(-5deg) scaleX(0.5);
  }
  .title .step-1 { left: 72px;  top: 371px; }
  .title .step-2 { left: 204px; top: 611px; }
  .title .step-3 { left: 420px; top: 758px; }
  .genre {
    position: absolute;
    bottom: 34px;
    left: 0;
    width: 724px;
    text-align: center;
    font-family: 'Cinzel', serif;
    font-weight: 700;
    font-size: 38px;
    letter-spacing: 17px;
    padding-left: 17px;
    box-sizing: border-box;
    color: var(--ink-navy);
    margin: 0;
  }
</style>
</head>
<body>
<main class="cover">
  <div class="ice-surface" role="img" aria-label="Helle, zarte Eisfläche mit feinen Strukturen"></div>

  <svg class="cracks" viewBox="0 0 724 1200" aria-hidden="true">
    <path d="M230 0 L270 60 L262 110 L300 160 L330 260 L360 330 L385 390 L400 440"/>
    <path d="M410 0 L455 30 L480 60 L470 110 L500 150 L495 200 L460 250 L450 280"/>
    <path d="M560 600 L545 660 L505 690 L510 760 L530 800 L520 850 L560 900 L590 980 L575 1060 L540 1100 L505 1200"/>
    <path d="M270 640 L240 655 L185 680 L150 700 L155 760 L130 800 L145 860 L165 910 L150 960 L120 1000 L115 1060 L100 1120 L110 1200"/>
    <path class="fine" d="M640 500 L680 560 L700 620 L690 700 L720 740"/>
    <path class="fine" d="M0 380 L40 410 L70 400 L110 440"/>
    <path class="fine" d="M620 900 L660 930 L700 920 L724 950"/>
  </svg>

  <div class="blue-dragon" role="img" aria-label="Blauer Drache (Glaucus atlanticus), der vom rechten Rand auf das Eis ragt"></div>

  <p class="author">KONRAD WEILER</p>

  <h1 class="title" aria-label="Kaltgrund">
    <span class="step-1">KAL</span>
    <span class="step-2">TGR</span>
    <span class="step-3">UND</span>
  </h1>

  <p class="genre">THRILLER</p>
</main>
</body>
</html>
```